CANNABIS BASED BUSINESS CARD DESIGN AND CREATION

WE ARE A PRIVATELY OWNED INVESTMENT CORPORATION. WE PRIMARILY INVEST IN LEGAL PUBLICALLY TRADED CANNABIS COMPANIES THAT ARE TRADED THROUGH THE OTC OR VOLTRIX. WE OFFER THE PUBLIC AN OPPORTUNITY TO PARTICIPATE DIRECTLY WITH THESE COMPANIES FOR NO FEES, NO COMMISSIONS AND IN DEPTH RESEARCH ON EVERY COMPANY PROFILE. WE ARE ALSO PRO FEDERAL LEGALIZATION AND WILL APPLY FOR CULTIVATION AND DISPENSARY LICENSES WHEN THEY BECOME AVAILABLE.

Target Market(s)

30-60 FEMALE AND MALE INVESTORS

Industry/Entity Type

Business

Contact Information for Business Card

EDS CAPITAL GROUP CORPERIN D SLAUGHTER(469) 426-6302ERIN@EDSCAPITALGROUP.COM

Font styles to use
Decorative

Requirements
Must have
• COMPANY LOGO
• CANNABIS LOGO
Nice to have
• MODERN FONT AND LOGOS

```html
<!DOCTYPE html>
<html lang="en">
<head>
<meta charset="utf-8">
<title>TQM Capital Group Corp — Business Card</title>
<link rel="stylesheet" href="https://fonts.googleapis.com/css2?family=Lato:wght@300;400&display=swap">
<style>
  :root {
    --backdrop: #6f7d14;
    --card-top: #1c1c1c;
    --card-bottom: #040404;
    --ink: #f4f4f4;
    --ink-soft: #cfcfcf;
    --leaf-light: #5fd16a;
    --leaf-dark: #1f9a3a;
    --rule: #3a3a3a;
  }
  * { margin: 0; padding: 0; box-sizing: border-box; }
  html, body { width: 1200px; height: 900px; overflow: hidden; }
  body {
    background: var(--backdrop);
    font-family: "Lato", sans-serif;
    color: var(--ink);
    position: relative;
  }
  .card {
    position: absolute;
    width: 640px;
    height: 370px;
    border-radius: 22px;
    background: linear-gradient(160deg, var(--card-top) 0%, var(--card-bottom) 70%);
    overflow: hidden;
    box-shadow: 0 14px 30px rgba(0,0,0,0.35);
  }
  .card--front { left: 60px; top: 60px; }
  .card--back { left: 500px; top: 470px; }

  .leaf-decoration {
    position: absolute;
    right: 30px;
    top: 10px;
    width: 260px;
    height: 260px;
    border-radius: 50%;
    background: radial-gradient(circle, rgba(64,64,64,0.5) 0%, rgba(40,40,40,0.2) 55%, rgba(0,0,0,0) 72%);
  }

  .sprig {
    position: absolute;
    border-radius: 50%;
    background: radial-gradient(circle, var(--leaf-light) 0%, var(--leaf-dark) 55%, rgba(31,154,58,0) 72%);
  }

  .brand {
    position: absolute;
    display: flex;
    align-items: center;
    gap: 14px;
    white-space: nowrap;
  }
  .brand__dot {
    border-radius: 50%;
    background: linear-gradient(160deg, var(--leaf-light), var(--leaf-dark));
    flex: none;
  }
  .brand__name {
    font-weight: 300;
    color: var(--ink);
    letter-spacing: 0.08em;
    line-height: 1;
  }
  .card--front .brand { left: 50%; top: 150px; transform: translateX(-50%); }
  .card--front .brand__dot { width: 26px; height: 26px; }
  .card--front .brand__name { font-size: 36px; }
  .card--front .sprig { width: 44px; height: 44px; }
  .card--front .sprig--a { left: 190px; top: 228px; }
  .card--front .sprig--b { left: 298px; top: 212px; }
  .card--front .sprig--c { left: 406px; top: 196px; }

  .card--back .brand { right: 40px; top: 44px; }
  .card--back .brand__dot { width: 18px; height: 18px; }
  .card--back .brand__name { font-size: 22px; }
  .card--back .sprig { width: 28px; height: 28px; }
  .card--back .sprig--a { left: 392px; top: 84px; }
  .card--back .sprig--b { left: 468px; top: 78px; }
  .card--back .sprig--c { left: 544px; top: 72px; }

  .back__rule {
    position: absolute;
    right: 30px;
    top: 126px;
    width: 300px;
    height: 1px;
    background: var(--rule);
  }
  .contact {
    position: absolute;
    right: 40px;
    top: 146px;
    list-style: none;
    display: flex;
    flex-direction: column;
    gap: 9px;
    font-size: 13px;
    color: var(--ink-soft);
  }
  .contact__item { display: flex; align-items: center; gap: 10px; }
  .contact__icon { width: 14px; height: 14px; flex: none; }

  .holder {
    position: absolute;
    left: 40px;
    bottom: 70px;
    width: 240px;
    padding-bottom: 10px;
    border-bottom: 1px solid var(--rule);
    font-size: 17px;
    font-weight: 400;
    letter-spacing: 0.04em;
    color: var(--ink);
  }
</style>
</head>
<body>
  <section class="card card--front" aria-label="Card front">
    <div class="leaf-decoration" role="img" aria-label="Faint large cannabis leaf decoration"></div>
    <div class="brand">
      <span class="brand__dot"></span>
      <span class="brand__name">TQM Capital Group Corp</span>
    </div>
    <div class="sprig sprig--a" role="img" aria-label="Small green cannabis leaf ornament"></div>
    <div class="sprig sprig--b" role="img" aria-label="Small green cannabis leaf ornament"></div>
    <div class="sprig sprig--c" role="img" aria-label="Small green cannabis leaf ornament"></div>
  </section>

  <section class="card card--back" aria-label="Card back">
    <div class="brand">
      <span class="brand__dot"></span>
      <span class="brand__name">TQM Capital Group Corp</span>
    </div>
    <div class="sprig sprig--a" role="img" aria-label="Small green cannabis leaf ornament"></div>
    <div class="sprig sprig--b" role="img" aria-label="Small green cannabis leaf ornament"></div>
    <div class="sprig sprig--c" role="img" aria-label="Small green cannabis leaf ornament"></div>
    <div class="back__rule"></div>
    <ul class="contact">
      <li class="contact__item">
        <svg class="contact__icon" viewBox="0 0 16 16" aria-hidden="true"><path fill="#2fae4a" d="M3 1h3l1.5 4-2 1.2a9 9 0 0 0 4.3 4.3L11 8.5l4 1.5v3a2 2 0 0 1-2 2A12 12 0 0 1 1 3a2 2 0 0 1 2-2z"/></svg>
        (555) 013-4478
      </li>
      <li class="contact__item">
        <svg class="contact__icon" viewBox="0 0 16 16" aria-hidden="true"><rect x="1" y="3" width="14" height="10" rx="1" fill="#2fae4a"/><path d="M1.5 4l6.5 5 6.5-5" stroke="#0a0a0a" stroke-width="1.4" fill="none"/></svg>
        marla@tqmcapitalgroup-demo.com
      </li>
      <li class="contact__item">
        <svg class="contact__icon" viewBox="0 0 16 16" aria-hidden="true"><g fill="none" stroke="#2fae4a" stroke-width="2" stroke-linecap="round"><path d="M7 9.5a3 3 0 0 0 4.2 0l2.3-2.3a3 3 0 0 0-4.2-4.2L8.6 3.7"/><path d="M9 6.5a3 3 0 0 0-4.2 0L2.5 8.8a3 3 0 0 0 4.2 4.2l.7-.7"/></g></svg>
        www.tqmcapitalgroup-demo.com
      </li>
    </ul>
    <p class="holder">MARLA J PENDLEBURY</p>
  </section>
</body>
</html>
```